Website for BrightlineLabs presentation

We need a new website, ideally as a wordpress there, for BrightlineLabs - we focus on machine learning, big data, data science and data analytics. This website should have two main sections - team presentation, introduction and offered services as static pages, and a blog section.

Target Market(s)

Companies which would like to hire the consultants for data science

Industry/Entity Type

Data Service

Font styles to use
Sans Serif

Colors

Designer to choose colors to be used in the design.

Requirements
Must have
• Wordpress template, blog and presentation pages, nice background images, incorporate the existing logo from brief
Nice to have
• match the word and ppt existing templates for brightline labs

```html
<!DOCTYPE html>
<html lang="en">
<head>
<meta charset="utf-8">
<title>BrightlineLabs</title>
<link href="https://fonts.googleapis.com/css2?family=Open+Sans:wght@400;600;700;800&display=swap" rel="stylesheet">
<style>
:root{
  --blue:#1a6fb5;
  --blue-deep:#0b3ea8;
  --navy:#0a1a3a;
  --ink:#1b1b1b;
  --text:#555;
  --muted:#777;
  --light:#f0f0f0;
  --faint:#ececec;
  --accent:#e0542e;
  --white:#fff;
  --bar:#4f4f4f;
}
*{box-sizing:border-box;margin:0;padding:0}
html,body{width:1200px;height:3396px;overflow:hidden}
body{font-family:"Open Sans",Arial,sans-serif;color:var(--ink);background:var(--white);position:relative}
.abs{position:absolute}
a{color:inherit;text-decoration:none}

/* header */
.brand{left:75px;top:22px;display:flex;align-items:center;gap:10px}
.brand-dot{width:36px;height:36px;border-radius:50%;background:var(--blue)}
.brand-name{font-weight:800;font-size:18px;line-height:20px;color:var(--blue);width:120px}
.nav{left:577px;top:36px;display:flex;align-items:center;font-size:14px;font-weight:600}
.nav-home{width:39px;height:39px;background:var(--blue);display:flex;align-items:center;justify-content:center;margin-right:42px}
.nav a.link{margin-right:39px}

/* hero */
.hero{left:0;top:109px;width:1200px;height:571px;clip-path:polygon(0 0,100% 0,100% 484px,0 571px);
  background:radial-gradient(ellipse at 55% 30%,#1f7fd0 0%,#0d3a78 45%,#061a3a 100%)}
.hero-box{left:215px;top:294px;width:792px;height:234px;border:1px solid rgba(255,255,255,.8);background:rgba(6,26,58,.55);text-align:center;color:var(--white)}
.hero-title{margin-top:26px;font-size:28px;font-weight:700}
.hero-text{margin:10px auto 0;width:660px;font-size:14px;line-height:22px}
.btn{display:inline-flex;align-items:center;gap:12px;font-weight:700;font-size:13px;color:var(--white);background:var(--blue);text-transform:uppercase}
.hero-btn{margin-top:20px;height:38px;padding:0 24px}
.arrow{top:372px}

/* years band */
.years{left:0;top:680px;width:1200px;height:169px;background:var(--light)}
.years-head{left:59px;top:693px;font-weight:700;font-size:29px;line-height:44px;color:var(--ink);text-align:center;width:400px}
.years-head b{font-size:48px;color:var(--blue);vertical-align:-4px;margin-right:6px}
.years-line{left:475px;top:700px;width:1px;height:135px;background:#d6d6d6}
.years-dot{left:465px;top:745px;width:26px;height:26px;border-radius:50%;background:var(--blue)}
.years-text{left:503px;top:708px;width:630px;font-size:14px;line-height:23px;color:var(--text)}

/* about */
.ghost{font-weight:800;color:var(--faint);text-transform:uppercase;letter-spacing:1px}
.about-ghost{left:136px;top:862px;font-size:58px}
.about-mark{left:75px;top:890px;width:44px;height:44px;border-radius:50%;background:var(--blue)}
.about-title{left:129px;top:920px;font-size:23px;font-weight:600}
.about-title b{font-weight:800}
.about-lead{left:75px;top:988px;width:520px;font-size:14px;font-weight:700;line-height:23px;color:#333}
.about-body{left:75px;top:1055px;width:520px;font-size:12.5px;line-height:23px;color:var(--muted)}
.about-btn{left:75px;top:1184px;height:38px;padding:0 18px}
.svc{width:260px}
.svc svg{display:block;margin-bottom:10px}
.svc h3{font-size:15px;font-weight:700;margin-bottom:6px}
.svc p{font-size:12.5px;line-height:21px;color:var(--muted)}

/* team */
.team{left:0;top:1268px;width:1200px;height:600px;clip-path:polygon(0 52px,100% 0,100% 543px,0 600px);
  background:linear-gradient(120deg,#14508f 0%,#2a7ac4 45%,#1a5ea8 70%,#0e3f7c 100%)}
.team-ghost{left:0;top:1318px;width:1200px;text-align:center;font-size:56px;color:rgba(255,255,255,.12)}
.team-title{left:0;top:1386px;width:1200px;text-align:center;font-size:22px;font-weight:700;color:var(--white)}
.team-rule{left:580px;top:1428px;width:40px;height:3px;background:var(--accent)}
.avatar{border-radius:50%;border:4px solid var(--white);background:linear-gradient(160deg,#bfc7d1,#7d8896)}
.team-text{left:267px;top:1636px;width:666px;text-align:center;font-size:12.5px;line-height:22px;color:var(--white)}
.team-btn{left:528px;top:1734px;height:36px;padding:0 22px;background:#4a4a4a}

/* blog */
.blog-ghost{left:0;top:1905px;width:1200px;text-align:center;font-size:58px}
.blog-title{left:0;top:1982px;width:1200px;text-align:center;font-size:22px;font-weight:600}
.blog-title b{font-weight:800}
.post-img{width:249px;height:185px}
.post-date{font-size:13px;font-weight:700;color:var(--blue)}
.post-title{font-size:18px;font-weight:600;line-height:25px;width:250px}
.post-text{left:643px;top:2146px;width:460px;font-size:14px;line-height:27px;color:var(--muted)}
.blog-btn{left:643px;top:2271px;height:41px;padding:0 28px;font-size:12px}

/* contact */
.contact{left:0;top:2355px;width:1200px;height:679px;clip-path:polygon(0 124px,100% 0,100% 100%,0 100%);
  background:linear-gradient(110deg,#1a4fb8 0%,#0b3aa6 50%,#0a2f8c 100%)}
.contact-head{left:79px;top:2598px;font-size:39px;font-weight:800;line-height:52px;color:var(--white);text-transform:uppercase}
.contact-rule{left:79px;top:2822px;width:45px;height:3px;background:#57c3e6}
.contact-text{left:79px;top:2848px;width:500px;font-size:12.5px;line-height:23px;color:var(--white)}
.form{left:747px;top:2497px;width:381px;height:491px;background:var(--white);border-radius:4px}
.field{left:40px;width:300px;font-size:14px;color:var(--ink);border-bottom:1px solid #cfcfcf;padding-bottom:10px}
.form-btn{left:138px;top:421px;height:37px;padding:0 22px}

/* footer */
.foot-brand{left:75px;top:3056px;display:flex;align-items:center;gap:10px}
.foot-about{left:75px;top:3145px;width:280px;font-size:12.5px;line-height:23px;color:#333}
.foot-btn{left:75px;top:3276px;height:32px;padding:0 16px;font-size:11px;background:var(--blue-deep)}
.foot-h{font-size:20px;color:var(--ink)}
.foot-rule{width:44px;height:3px;background:var(--blue)}
.foot-list{list-style:none;font-size:13px;line-height:27.6px;color:#222}
.foot-list li{display:flex;align-items:flex-start;gap:14px}
.foot-list svg{flex:none;margin-top:8px}
.social{width:26px;height:26px;border-radius:50%}
.bottom{left:0;top:3362px;width:1200px;height:34px;background:var(--bar);color:var(--white);font-size:12px;text-align:center;line-height:34px}
.bottom b{margin-left:6px}
</style>
</head>
<body>

<header>
  <div class="abs brand"><span class="brand-dot"></span><span class="brand-name">BRIGHTLINE LABS</span></div>
  <nav class="abs nav">
    <span class="nav-home"><svg width="18" height="16" viewBox="0 0 18 16"><path d="M9 1 1 8h2.5v7h4v-5h3v5h4V8H17z" fill="#fff"/></svg></span>
    <a class="link" href="#about">ABOUT US</a>
    <a class="link" href="#services">SERVICES</a>
    <a class="link" href="#team">TEAM</a>
    <a class="link" href="#blog">BLOG</a>
    <a class="link" href="#contact">CONTACT US</a>
  </nav>
</header>

<section class="abs hero" role="img" aria-label="Glowing blue circuit board network background"></section>
<svg class="abs arrow" style="left:116px" width="26" height="30" viewBox="0 0 26 30"><path d="M18 4 7 15l11 11" stroke="#fff" stroke-width="4" fill="none"/></svg>
<svg class="abs arrow" style="left:1066px" width="26" height="30" viewBox="0 0 26 30"><path d="M8 4l11 11L8 26" stroke="#fff" stroke-width="4" fill="none"/></svg>
<div class="abs hero-box">
  <h1 class="hero-title">BRIGHTLINE LABS</h1>
  <p class="hero-text">Sapien vestibulum non. At ut sed ligula animi nunc mauris blandit non nulla lacinia duis. Senectus ac tincidunt. Sapien commodo nulla. Pede quam sollicitudin vivamus elit porta.</p>
  <a class="btn hero-btn" href="#contact">Free consultation <svg width="8" height="12" viewBox="0 0 8 12"><path d="M1 1l5 5-5 5" stroke="#fff" stroke-width="2" fill="none"/></svg></a>
</div>

<section class="abs years"></section>
<h2 class="abs years-head"><b>25</b> YEARS OF QUALITY<br>SERVICE IN DATA SCIENCE</h2>
<span class="abs years-line"></span>
<span class="abs years-dot"><svg width="26" height="26" viewBox="0 0 26 26"><path d="M11 8l5 5-5 5" stroke="#fff" stroke-width="2" fill="none"/></svg></span>
<p class="abs years-text">Duis aute irure dolor in reprehenderit in voluptate velit esse cillum dolore eu fugiat nulla pariatur. Excepteur sint occaecat cupidatat non proident, sunt in culpa qui officia deserunt mollit anim id est laborum. Consect petur adipiscing elit. eu fugiat nulla pariatur. Excepteur sint occaecat</p>

<section id="about">
  <div class="abs ghost about-ghost">About</div>
  <span class="abs about-mark"></span>
  <h2 class="abs about-title">BRIGHTLINE <b>LABS</b></h2>
  <p class="abs about-lead">Gravida consectetuer pede laoreet ac a non leo non tellus amet vel. Magna suspendisse vestibulum.</p>
  <p class="abs about-body">Convallis curabitur vestibulum. Justo rutrum a. A ut arcu felis eget litora libero ligula morbi vestibulum eu tellus vel consectetur congue. Ultricies et commodo amet accumsan nunc eget mattis tincidunt nonummy donec viverra sed nec iaculis consectetuer lectus dictum. Velit iaculis a.</p>
  <a class="abs btn about-btn" href="#about">Read more <svg width="8" height="12" viewBox="0 0 8 12"><path d="M1 1l5 5-5 5" stroke="#fff" stroke-width="2" fill="none"/></svg></a>
</section>

<section id="services">
  <div class="abs svc" style="left:623px;top:883px">
    <svg width="48" height="46" viewBox="0 0 48 46" fill="none" stroke="#1a6fb5" stroke-width="2"><rect x="10" y="4" width="34" height="26"/><path d="M4 42h40M16 22l6-6 6 4 8-9"/><circle cx="8" cy="30" r="5"/></svg>
    <h3>Machine learning</h3>
    <p>Enim aliquam nihil. Id mauris turpis. Condimentum pellentesque urna. Sapien vestibulum non.</p>
  </div>
  <div class="abs svc" style="left:899px;top:883px">
    <svg width="48" height="46" viewBox="0 0 48 46" fill="none" stroke="#1a6fb5" stroke-width="2"><rect x="4" y="4" width="40" height="30"/><path d="M12 28V18M20 28V12M28 28V20M36 28V10M16 42h16"/></svg>
    <h3>Big data</h3>
    <p>Enim aliquam nihil. Id mauris turpis. Condimentum pellentesque urna. Sapien vestibulum non.</p>
  </div>
  <div class="abs svc" style="left:623px;top:1062px">
    <svg width="48" height="46" viewBox="0 0 48 46" fill="none" stroke="#1a6fb5" stroke-width="2"><rect x="6" y="4" width="34" height="38"/><path d="M12 14h22M12 22h22M12 30h14"/></svg>
    <h3>Data science</h3>
    <p>Enim aliquam nihil. Id mauris turpis. Condimentum pellentesque urna. Sapien vestibulum non.</p>
  </div>
  <div class="abs svc" style="left:899px;top:1062px">
    <svg width="48" height="46" viewBox="0 0 48 46" fill="none" stroke="#1a6fb5" stroke-width="2"><circle cx="20" cy="20" r="14"/><path d="M30 30l12 12M13 24l5-5 4 3 6-7"/></svg>
    <h3>Data analytics</h3>
    <p>Enim aliquam nihil. Id mauris turpis. Condimentum pellentesque urna. Sapien vestibulum non.</p>
  </div>
</section>

<section id="team">
  <div class="abs team" role="img" aria-label="Team of consultants in a meeting, blue tinted photo"></div>
  <div class="abs ghost team-ghost">Our team</div>
  <h2 class="abs team-title">TEAM</h2>
  <span class="abs team-rule"></span>
  <div class="abs avatar" style="left:344px;top:1499px;width:90px;height:90px" role="img" aria-label="Team member portrait"></div>
  <div class="abs avatar" style="left:428px;top:1490px;width:108px;height:108px" role="img" aria-label="Team member portrait"></div>
  <div class="abs avatar" style="left:533px;top:1478px;width:132px;height:132px" role="img" aria-label="Team member portrait"></div>
  <div class="abs avatar" style="left:652px;top:1490px;width:108px;height:108px" role="img" aria-label="Team member portrait"></div>
  <div class="abs avatar" style="left:752px;top:1499px;width:90px;height:90px" role="img" aria-label="Team member portrait"></div>
  <p class="abs team-text">Convallis curabitur vestibulum. Justo rutrum a. A ut arcu felis eget litora libero ligula morbi vestibulum eu tellus vel consectetur congue. Ultricies et commodo amet accumsan nunc eget mattis tincidunt nonummy donec viverra sed nec iaculis consectetuer lectus dictum. Velit iaculis a.</p>
  <a class="abs btn team-btn" href="#team">Read more <svg width="8" height="12" viewBox="0 0 8 12"><path d="M1 1l5 5-5 5" stroke="#fff" stroke-width="2" fill="none"/></svg></a>
</section>

<section id="blog">
  <div class="abs ghost blog-ghost">Our recent post</div>
  <h2 class="abs blog-title">OUR <b>BLOG</b></h2>
  <div class="abs post-img" style="left:72px;top:2081px;background:radial-gradient(circle at 62% 30%,#f5e7a8 0%,#2a5da8 22%,#0a1d45 70%)" role="img" aria-label="Light bulb on a glowing circuit board"></div>
  <div class="abs post-date" style="left:72px;top:2283px">8-JAN-2018</div>
  <div class="abs post-title" style="left:72px;top:2312px">Pellentesque molestie ante and consectetur...</div>
  <div class="abs post-img" style="left:346px;top:2081px;background:linear-gradient(180deg,#3c5f8e 0%,#1a2d4d 60%,#0d1629 100%)" role="img" aria-label="Person standing in a server room aisle"></div>
  <div class="abs post-date" style="left:346px;top:2283px">8-JAN-2018</div>
  <div class="abs post-title" style="left:346px;top:2312px">Integer vitaeneque vel augue malesuada...</div>
  <div class="abs post-date" style="left:643px;top:2089px">8-JAN-2018</div>
  <div class="abs post-title" style="left:643px;top:2114px;width:460px">Curabitur porta sapienne tortor ornare</div>
  <p class="abs post-text">Lorem Ipsum is simply dummy text of the printing typesetting industry. Lorem Ipsum has been the industry's standard dummy text ever since...</p>
  <a class="abs btn blog-btn" href="#blog">Check all blogs</a>
</section>

<section id="contact">
  <div class="abs contact" role="img" aria-label="Deep blue abstract network background"></div>
  <h2 class="abs contact-head">If you have a<br>question,<br>you can contact us.<br>Just fill a form.</h2>
  <span class="abs contact-rule"></span>
  <p class="abs contact-text">At ut sed ligula animi nunc mauris blandit non nulla lacinia duis. Senectus ac tincidunt. Sapien commodo nulla. Pede quam sollicitudin vivamus elit porta. Etiam ut nisl vestibulum maecenas vestibulum velit suscipit porta. Mollit in pretium sollicitudin semper magna quia nibh vitae. Gravida consectetuer pede laoreet ac a non leo non tellus amet vel. Magna suspendisse vestibulum.</p>
  <form class="abs form">
    <div class="abs field" style="top:48px">Name</div>
    <div class="abs field" style="top:113px">Email</div>
    <div class="abs field" style="top:179px">Phone</div>
    <div class="abs field" style="top:253px;height:136px">Message</div>
    <span class="abs btn form-btn">Send <svg width="8" height="12" viewBox="0 0 8 12"><path d="M1 1l5 5-5 5" stroke="#fff" stroke-width="2" fill="none"/></svg></span>
  </form>
</section>

<footer>
  <div class="abs foot-brand"><span class="brand-dot"></span><span class="brand-name">BRIGHTLINE LABS</span></div>
  <p class="abs foot-about">Donec et varius lacinia pellentesque vivamus. Ultrices nec tincidunt. Sed libero nostra in tempor eu. Vitae mauris in elit aliquam dolor tempus ipsum libero. Non pellentesque erat. Duis erat condimentum.</p>
  <a class="abs btn foot-btn" href="#about">More <svg width="7" height="10" viewBox="0 0 8 12"><path d="M1 1l5 5-5 5" stroke="#fff" stroke-width="2" fill="none"/></svg></a>

  <div class="abs" style="left:437px;top:3072px">
    <h3 class="foot-h">Quick Links</h3>
    <div class="foot-rule" style="margin:6px 0 28px"></div>
    <ul class="foot-list">
      <li><svg width="6" height="10" viewBox="0 0 6 10"><path d="M1 1l4 4-4 4" stroke="#222" stroke-width="1.5" fill="none"/></svg>Home</li>
      <li><svg width="6" height="10" viewBox="0 0 6 10"><path d="M1 1l4 4-4 4" stroke="#222" stroke-width="1.5" fill="none"/></svg>About Us</li>
      <li><svg width="6" height="10" viewBox="0 0 6 10"><path d="M1 1l4 4-4 4" stroke="#222" stroke-width="1.5" fill="none"/></svg>Service</li>
      <li><svg width="6" height="10" viewBox="0 0 6 10"><path d="M1 1l4 4-4 4" stroke="#222" stroke-width="1.5" fill="none"/></svg>Team</li>
      <li><svg width="6" height="10" viewBox="0 0 6 10"><path d="M1 1l4 4-4 4" stroke="#222" stroke-width="1.5" fill="none"/></svg>Blog</li>
      <li><svg width="6" height="10" viewBox="0 0 6 10"><path d="M1 1l4 4-4 4" stroke="#222" stroke-width="1.5" fill="none"/></svg>Contact Us</li>
    </ul>
  </div>

  <div class="abs" style="left:650px;top:3068px;width:250px">
    <h3 class="foot-h">Contact Us</h3>
    <div class="foot-rule" style="margin:6px 0 28px"></div>
    <ul class="foot-list">
      <li><svg width="10" height="13" viewBox="0 0 10 13"><path d="M5 0a5 5 0 0 0-5 5c0 4 5 8 5 8s5-4 5-8a5 5 0 0 0-5-5z" fill="#222"/><circle cx="5" cy="5" r="2" fill="#fff"/></svg><span>9870 Lorium ipsum,Dolor amit,<br>City name. country.</span></li>
      <li><svg width="12" height="12" viewBox="0 0 12 12"><path d="M2 0l3 3-1.5 1.8a8 8 0 0 0 3.7 3.7L9 7l3 3-2 2C5 12 0 7 0 2z" fill="#222"/></svg>+1 800 555 0135</li>
      <li><svg width="12" height="12" viewBox="0 0 12 12"><rect x="0" y="4" width="12" height="8" fill="#222"/><rect x="3" y="0" width="6" height="4" fill="#222"/></svg>+1 800 555 0198</li>
      <li><svg width="12" height="10" viewBox="0 0 12 10"><rect width="12" height="10" fill="#222"/><path d="M0 1l6 4 6-4" stroke="#fff" fill="none"/></svg>info@brightlinelabs.example</li>
    </ul>
  </div>

  <div class="abs" style="left:951px;top:3072px">
    <h3 class="foot-h">Follow Us</h3>
    <div class="foot-rule" style="margin:6px 0 0"></div>
  </div>
  <span class="abs social" style="left:951px;top:3141px;background:#3b5998"></span>
  <span class="abs social" style="left:985px;top:3141px;background:#2a9fd8"></span>
  <span class="abs social" style="left:1019px;top:3141px;background:#d9442f"></span>
  <span class="abs social" style="left:1053px;top:3141px;background:#8a3ab9"></span>
  <span class="abs social" style="left:1087px;top:3141px;background:#1c6fa8"></span>

  <div class="abs bottom">© 2018 | <b>brightline labs</b></div>
</footer>

</body>
</html>
```